High end Electrical/home automation Business Card

Need a card for a high end electrical and home automation company utilising the existing logo.
Phone
Email
Website

Like black look with raised detail. Don’t necessarily need to keep colour of logo it could be made grayscale or white etc

Target Market(s)

High end clients

Contact Information for Business Card

Brightmoor Electrical

Requirements
Must have
• Logo, phone, email, website, address

High end look
Nice to have
• Black background card
Raised font
Should not have
• Lots of colour

```html
<!DOCTYPE html>
<html lang="en">
<head>
<meta charset="utf-8">
<title>Brightmoor Electrical – Business Card</title>
<link href="https://fonts.googleapis.com/css2?family=Montserrat:wght@400;500;600;700&display=swap" rel="stylesheet">
<style>
  :root {
    --backdrop: #b0b0ac;
    --paper: #ffffff;
    --ink: #333335;
    --ink-soft: #4a4a4d;
    --accent: #0a8ad6;
    --card-dark: #353537;
    --on-dark: #ffffff;
  }
  * { box-sizing: border-box; margin: 0; padding: 0; }
  html, body {
    width: 1200px; height: 801px; overflow: hidden;
    background: var(--backdrop);
    font-family: "Montserrat", Arial, sans-serif;
  }
  .stage {
    position: relative; width: 1200px; height: 801px;
    display: flex; align-items: center; justify-content: center; gap: 40px;
  }
  .card {
    position: relative; width: 540px; height: 309px;
    border-bottom: 5px solid var(--accent);
    box-shadow: 0 14px 30px rgba(0,0,0,.22);
  }
  /* Front side */
  .card-front { background: var(--paper); color: var(--ink); }
  .brand-front {
    position: absolute; top: 40px; right: 44px;
    display: flex; align-items: center; gap: 10px;
  }
  .brand-dot { width: 16px; height: 16px; border-radius: 50%; background: var(--accent); }
  .brand-name { font-weight: 700; font-size: 21px; color: var(--ink); letter-spacing: -.2px; }
  .rule-top {
    position: absolute; top: 100px; left: 200px; right: 40px;
    height: 1px; background: var(--accent);
  }
  .address {
    position: absolute; top: 116px; right: 44px; text-align: right;
    font-size: 13px; line-height: 1.45; color: var(--ink-soft);
  }
  .person { position: absolute; left: 60px; top: 150px; }
  .person-name { font-size: 21px; font-weight: 500; color: var(--accent); letter-spacing: 1px; }
  .person-role { font-size: 14px; color: var(--ink-soft); margin-top: 2px; }
  .rule-bottom {
    position: absolute; left: 60px; width: 300px; top: 213px;
    height: 1px; background: var(--accent);
  }
  .contact-list {
    position: absolute; left: 60px; top: 224px; list-style: none;
    font-size: 14px; line-height: 1.45; color: var(--ink);
  }
  .contact-list li { display: flex; align-items: center; gap: 8px; }
  .contact-list svg { width: 11px; height: 11px; flex: none; }
  .edge-tab {
    position: absolute; left: 0; top: 228px; width: 12px; height: 30px;
    background: var(--accent);
  }
  /* Back side */
  .card-back { background: var(--card-dark); }
  .brand-back {
    position: absolute; left: 44px; bottom: 40px;
    font-weight: 700; font-size: 30px; color: var(--on-dark); letter-spacing: -.3px;
  }
</style>
</head>
<body>
<main class="stage">
  <section class="card card-front" aria-label="Card front">
    <div class="brand-front">
      <span class="brand-dot"></span>
      <span class="brand-name">Brightmoor Electrical</span>
    </div>
    <div class="rule-top"></div>
    <address class="address" style="font-style:normal">418 Alder Lane<br>Kettle Ridge, WA 99000</address>
    <div class="person">
      <div class="person-name">DANIEL HART</div>
      <div class="person-role">Founder</div>
    </div>
    <div class="rule-bottom"></div>
    <ul class="contact-list">
      <li>
        <svg viewBox="0 0 12 12" aria-hidden="true"><path d="M2.5 1 L4.5 1 L5 3.5 L3.8 4.4 Q5 7 7.6 8.2 L8.5 7 L11 7.5 L11 9.5 Q10.5 11 9 11 Q1 10 1 3 Q1 1.5 2.5 1Z" fill="var(--accent)"/></svg>
        555 310 4826
      </li>
      <li>
        <svg viewBox="0 0 12 12" aria-hidden="true"><rect x="1" y="2.5" width="10" height="7" fill="none" stroke="var(--accent)" stroke-width="1.2"/><path d="M1 2.5 L6 6.5 L11 2.5" fill="none" stroke="var(--accent)" stroke-width="1.2"/></svg>
        hello@brightmoor.com
      </li>
      <li>
        <svg viewBox="0 0 12 12" aria-hidden="true"><circle cx="6" cy="6" r="5" fill="none" stroke="var(--accent)" stroke-width="1.2"/><ellipse cx="6" cy="6" rx="2.2" ry="5" fill="none" stroke="var(--accent)" stroke-width="1"/><path d="M1 6 H11" stroke="var(--accent)" stroke-width="1"/></svg>
        brightmoorelectrical.com
      </li>
    </ul>
    <div class="edge-tab"></div>
  </section>

  <section class="card card-back" aria-label="Card back">
    <div class="brand-back">Brightmoor Electrical</div>
  </section>
</main>
</body>
</html>
```